Computer Repair Business - Needs New Business Card Design

I want to create a very cool business card for my business. I want to make it 100% different from my previous card. I would like to use similar color scheme like Royal blue.

With this card I want to create a conversation and have my customers say "Wow, that's a cool business card" Trying to prevent it from looking like the typical card that get's shoved into a wallet.

My website is below:

www.lornapcfix.com

I want to edit the hours and website and email:

www.lornapcfix.com
lorna@lornapcfix.com

10:30 to 6pm Monday - Friday
10:30 to 3pm Saturday
Updates

Just to remind, when i see a new design i don't want to notice my old design.

Business card will be printed and made with rounded corners and horizontal.

The back of the card should say " In-Store Repair, Remote Support, Data Recovery"

Industry/Entity Type

Business

Font styles to use
Sans Serif

Colors
33a6d7
3176b5

Requirements
Must have
• Clean looking - have creative aspects.
Should not have
• Should not look like the previous card design.

```html
<!DOCTYPE html>
<html lang="en">
<head>
<meta charset="utf-8">
<title>Lorna PC Fix – Business Card</title>
<link href="https://fonts.googleapis.com/css2?family=Roboto:wght@300;400;500&display=swap" rel="stylesheet">
<style>
  :root {
    --royal: #1f5fb0;
    --steel: #a9adb2;
    --ink: #2e3338;
    --paper: #ffffff;
    --backdrop: #e7e8ea;
  }
  * { margin: 0; padding: 0; box-sizing: border-box; }
  html, body { width: 1200px; height: 901px; overflow: hidden; }
  body {
    background: var(--backdrop);
    font-family: "Roboto", Arial, sans-serif;
    position: relative;
  }
  .card {
    position: absolute;
    left: 320px;
    width: 560px;
    height: 320px;
    background: var(--paper);
    border-radius: 14px;
    overflow: hidden;
    box-shadow: 0 4px 14px rgba(0,0,0,.12);
  }
  .card--front { top: 95px; }
  .card--back { top: 480px; }
  .card__bands { position: absolute; inset: 0; width: 100%; height: 100%; }

  /* front */
  .brand {
    position: absolute; left: 40px; top: 34px;
    display: flex; align-items: center; gap: 12px;
  }
  .brand__mark { width: 16px; height: 16px; background: var(--royal); }
  .brand__name {
    font-size: 34px; font-weight: 400; letter-spacing: 2px;
    color: var(--royal);
  }
  .brand__rule {
    position: absolute; left: 40px; top: 92px;
    width: 300px; height: 2px; background: var(--royal);
  }
  .person { position: absolute; left: 40px; top: 108px; color: var(--ink); }
  .person__name { font-size: 20px; font-weight: 500; letter-spacing: 1px; }
  .person__title { font-size: 12px; font-weight: 400; letter-spacing: 1.5px; margin-top: 2px; }
  .contacts { position: absolute; left: 40px; top: 176px; list-style: none; }
  .contacts li {
    display: flex; align-items: center; gap: 10px;
    font-size: 12px; color: var(--royal); height: 26px;
  }
  .contacts svg { width: 16px; height: 16px; flex: none; }
  .partner-badge {
    position: absolute; right: 26px; bottom: 22px;
    width: 80px; height: 20px; border-radius: 3px; background: var(--royal);
  }

  /* back */
  .hours {
    position: absolute; right: 30px; top: 28px; width: 340px; text-align: right;
    color: var(--royal);
  }
  .hours__main { font-size: 12px; letter-spacing: .2px; white-space: nowrap; }
  .hours__note { font-size: 11px; margin-top: 4px; }
  .services {
    position: absolute; left: 210px; right: 24px; top: 120px;
    display: flex; justify-content: space-between; list-style: none;
  }
  .service { width: 100px; text-align: center; color: var(--royal); }
  .service__icon {
    width: 42px; height: 42px; margin: 0 auto 10px;
    border-radius: 6px; background: linear-gradient(#c9ccd0, #8d9298);
  }
  .service__label { font-size: 14px; line-height: 1.2; }
</style>
</head>
<body>

<section class="card card--front" aria-label="Card front">
  <svg class="card__bands" viewBox="0 0 560 320" aria-hidden="true">
    <polygon points="470,0 520,0 400,320 350,320" fill="var(--royal)"/>
    <polygon points="520,0 560,0 560,40 452,320 400,320" fill="var(--steel)"/>
    <polygon points="560,60 560,150 494,320 460,320" fill="var(--royal)"/>
  </svg>

  <div class="brand">
    <span class="brand__mark"></span>
    <span class="brand__name">LORNA PC FIX</span>
  </div>
  <div class="brand__rule"></div>

  <div class="person">
    <p class="person__name">JORDAN PELL</p>
    <p class="person__title">FINANCIAL ADVISOR</p>
  </div>

  <ul class="contacts">
    <li>
      <svg viewBox="0 0 16 16"><rect width="16" height="16" rx="2" fill="var(--royal)"/><path d="M5 4l2 2-1 1c.6 1.3 1.7 2.4 3 3l1-1 2 2-1.5 1.5C7 12 4 9 3.5 5.5z" fill="#fff"/></svg>
      555 014 2270
    </li>
    <li>
      <svg viewBox="0 0 16 16"><rect width="16" height="16" rx="2" fill="var(--royal)"/><rect x="3.5" y="5" width="9" height="6" fill="none" stroke="#fff" stroke-width="1.2"/><path d="M3.5 5l4.5 3.5L12.5 5" fill="none" stroke="#fff" stroke-width="1.2"/></svg>
      lorna@lornapcfix.com
    </li>
    <li>
      <svg viewBox="0 0 16 16"><rect width="16" height="16" rx="2" fill="var(--royal)"/><circle cx="8" cy="8" r="4.5" fill="none" stroke="#fff" stroke-width="1.2"/><path d="M3.5 8h9M8 3.5c-2 2.5-2 6.5 0 9M8 3.5c2 2.5 2 6.5 0 9" fill="none" stroke="#fff" stroke-width="1"/></svg>
      www.lornapcfix.com
    </li>
    <li>
      <svg viewBox="0 0 16 16"><rect width="16" height="16" rx="2" fill="var(--royal)"/><path d="M8 13s-3.5-4-3.5-6.2a3.5 3.5 0 017 0C11.5 9 8 13 8 13z" fill="#fff"/><circle cx="8" cy="6.8" r="1.2" fill="var(--royal)"/></svg>
      12 Elm Row, Fairhaven, OR 97001
    </li>
  </ul>

  <div class="partner-badge" role="img" aria-label="Authorized partner badge"></div>
</section>

<section class="card card--back" aria-label="Card back">
  <svg class="card__bands" viewBox="0 0 560 320" aria-hidden="true">
    <polygon points="0,0 80,0 0,160" fill="var(--steel)"/>
    <polygon points="80,0 118,0 0,236 0,160" fill="var(--royal)"/>
    <polygon points="128,0 146,0 0,292 0,256" fill="var(--steel)"/>
    <polygon points="146,0 164,0 4,320 0,320 0,292" fill="var(--royal)"/>
  </svg>

  <div class="hours">
    <p class="hours__main">Hours / MON - FRI 10:30 am - 6:00 pm / SAT 10:30 am - 3:00 pm</p>
    <p class="hours__note">After hours support available by appointment</p>
  </div>

  <ul class="services">
    <li class="service">
      <div class="service__icon" role="img" aria-label="Screwdriver icon"></div>
      <p class="service__label">In-Store Repair</p>
    </li>
    <li class="service">
      <div class="service__icon" role="img" aria-label="Globe with support figure icon"></div>
      <p class="service__label">Remote Support</p>
    </li>
    <li class="service">
      <div class="service__icon" role="img" aria-label="Computer chip icon"></div>
      <p class="service__label">Data Recovery</p>
    </li>
  </ul>
</section>

</body>
</html>
```